Signage Design Project

We need a logo and signage for the shopfront of a personal fitness training gym and coaching facility. We want the signage to cover the glass shopfront windows which consist of 4 glass windows with dimensions: 1 of 200cm x 180cm, 2 of 180cm x 135cm and 1 of 180cm x 180cm. The windows that are 200x 180 and 180x180 are the most visable/ important. We want the 200x180 to display the logo and our name which is "Ridgeline Fitness Centre" with further information of: Your personal training studio and boutique coaching gym Ph: 9471 2836.
For the window with 180 x 180cm measurement we want to list the services we provide which are:
Personal Training Sessions | Group Classes|Weight Loss |Toning & Sculpting|Bodybuilding I Cardio|Weights| Kettlebells| Boxing| Circuits I Team Building Programs| Boot Camp I Healthy Lifestyle & Wellness Coaching
The 2 windows 180x135cm are diagonal to the entry of the shop. We want them to be the same and plainer in design with the words: Ridgeline Fitness Centre
Personal Training Studio and Boutique Coaching Gym
The signage design also includes an acrylic window box that lights up which is to display the logo and Ridgeline Fitness Centre

```html
<!DOCTYPE html>
<html lang="en">
<head>
<meta charset="utf-8">
<title>Ridgeline Fitness Centre – Services Window</title>
<link rel="stylesheet" href="https://fonts.googleapis.com/css2?family=Arimo:wght@700&display=swap">
<style>
  :root {
    --brand-blue: #0a9cc4;
    --accent-green: #a8b824;
    --deep-teal: #0e6f8c;
    --paper: #ffffff;
    --frame-grey: #8a8a8a;
    --edge: #333333;
  }
  * { margin: 0; padding: 0; box-sizing: border-box; }
  html, body { width: 1200px; height: 900px; overflow: hidden; background: var(--paper); }
  .canvas {
    position: relative;
    width: 1200px;
    height: 900px;
    border: 1px solid var(--frame-grey);
    background: var(--paper);
  }
  .window-panel {
    position: absolute;
    left: 237px;
    top: 87px;
    width: 708px;
    height: 718px;
    border: 1px solid var(--edge);
    background: var(--paper);
    overflow: hidden;
    font-family: "Arimo", Arial, sans-serif;
    font-weight: 700;
    color: var(--brand-blue);
  }
  .brand {
    position: absolute;
    left: 148px;
    top: 60px;
    display: flex;
    align-items: center;
    gap: 14px;
  }
  .brand-dot {
    width: 96px;
    height: 96px;
    border-radius: 50%;
    background: var(--brand-blue);
  }
  .brand-name { line-height: 1; text-transform: uppercase; }
  .brand-name .line-main { display: block; font-size: 58px; letter-spacing: 1px; }
  .brand-name .line-sub { display: block; font-size: 27px; letter-spacing: 2px; margin-top: 6px; text-transform: none; }
  .services {
    position: absolute;
    left: 0;
    top: 208px;
    width: 100%;
    list-style: none;
    text-align: center;
    font-size: 24px;
    letter-spacing: 0.2px;
  }
  .services li { height: 48px; line-height: 40px; white-space: nowrap; }
  .services .sep { color: var(--accent-green); margin: 0 4px; }
  .base-art { position: absolute; left: 0; top: 0; width: 708px; height: 718px; }
  .photo-slot {
    position: absolute;
    left: 371px;
    top: 443px;
    width: 328px;
    height: 262px;
    border-radius: 40px 40px 20px 60px;
    background: linear-gradient(160deg, #e9c9a8 0%, #6fb6d6 55%, #2e7fa8 100%);
  }
</style>
</head>
<body>
<div class="canvas">
  <section class="window-panel">
    <svg class="base-art" viewBox="0 0 708 718" aria-hidden="true">
      <path d="M0,490 C130,560 320,690 620,680 L620,718 L0,718 Z" fill="var(--accent-green)"/>
      <path d="M708,435 C690,560 640,665 470,718 L708,718 Z" fill="var(--deep-teal)"/>
      <path d="M0,545 C150,640 330,700 600,690" fill="none" stroke="var(--paper)" stroke-width="6"/>
      <circle cx="45" cy="668" r="20" fill="var(--paper)"/>
    </svg>

    <div class="brand">
      <span class="brand-dot"></span>
      <span class="brand-name">
        <span class="line-main">Ridgeline</span>
        <span class="line-sub">Fitness Centre</span>
      </span>
    </div>

    <ul class="services">
      <li>Personal Training Sessions <span class="sep">|</span> Group Classes</li>
      <li>Weight Loss <span class="sep">|</span> Toning &amp; Sculpting <span class="sep">|</span> Body Building</li>
      <li>Cardio <span class="sep">|</span> Weights <span class="sep">|</span> Kettlebells Boxing <span class="sep">|</span> Circuits</li>
      <li>Team Building Programs <span class="sep">|</span> Boot Camp</li>
      <li>Healthy Lifestyle &amp; Wellness Coaching</li>
    </ul>

    <div class="photo-slot" role="img" aria-label="Photo of a smiling woman in blue workout clothes seated on the floor, stretching her leg"></div>
  </section>
</div>
</body>
</html>
```